Stonebridge Building and Projects business cards

A business card with watermark background (construction work)

Company logo attached

Home improvement projects
House renovations
Bathroom and kitchen renovations
House extensions
New builds and granny flats

Director Omar Haddani
(Phone number)
omar@sbpbuilding.com.au
(Instagram logo) sbp_building

```html
<!DOCTYPE html>
<html lang="en">
<head>
<meta charset="utf-8">
<title>Stonebridge Building and Projects – Business Cards</title>
<link rel="stylesheet" href="https://fonts.googleapis.com/css2?family=Montserrat:wght@500;600;700&display=swap">
<style>
  :root {
    --page-bg: #444446;
    --brand-blue: #2e74b9;
    --card-blue: #0a6cb4;
    --card-blue-deep: #2c55ae;
    --ink-grey: #4a4a4a;
    --white: #ffffff;
  }
  * { box-sizing: border-box; margin: 0; padding: 0; }
  html, body { width: 1200px; height: 1200px; overflow: hidden; }
  body {
    background: var(--page-bg);
    font-family: "Montserrat", Arial, sans-serif;
    display: flex;
    flex-direction: column;
    align-items: center;
    justify-content: center;
    gap: 40px;
  }
  .card {
    position: relative;
    width: 840px;
    height: 480px;
    border-radius: 30px;
    overflow: hidden;
  }

  /* Services side */
  .card-services { background: var(--card-blue); color: var(--white); }
  .services-photo {
    position: absolute; inset: 0;
    background: linear-gradient(120deg, var(--card-blue) 0%, #1f62b3 45%, var(--card-blue-deep) 100%);
  }
  .services-content { position: relative; padding: 52px 60px; }
  .services-title { font-size: 42px; font-weight: 700; letter-spacing: 0.5px; margin-bottom: 10px; }
  .services-list { list-style: none; font-size: 25px; font-weight: 600; line-height: 1.12; }
  .services-list li::before { content: "·"; margin-right: 10px; }
  .services-brand {
    position: absolute; left: 60px; bottom: 46px;
    font-size: 34px; font-weight: 700; line-height: 1.1; width: 420px;
  }

  /* Contact side */
  .card-contact { background: var(--white); color: var(--brand-blue); }
  .contact-person { position: absolute; left: 42px; top: 200px; }
  .person-name { font-size: 54px; font-weight: 700; line-height: 1; }
  .person-role { font-size: 24px; font-weight: 500; margin-top: 4px; }
  .contact-list { position: absolute; left: 40px; top: 330px; list-style: none; }
  .contact-list li {
    display: flex; align-items: center; gap: 10px;
    font-size: 25px; font-weight: 600; height: 34px;
  }
  .contact-icon { width: 22px; height: 22px; flex: none; }
  .brand-lockup {
    position: absolute; left: 470px; top: 110px; width: 320px;
    display: flex; flex-direction: column; align-items: center; gap: 16px;
  }
  .brand-square { width: 28px; height: 28px; background: var(--brand-blue); }
  .brand-name { font-size: 32px; font-weight: 700; line-height: 1.15; text-align: center; }
  .social {
    position: absolute; left: 490px; top: 362px;
    font-size: 24px; font-weight: 600;
  }
  .social-handle { display: flex; align-items: center; gap: 12px; margin-top: 8px; }
  .social-dot { width: 22px; height: 22px; border-radius: 50%; background: var(--ink-grey); }
</style>
</head>
<body>

  <section class="card card-services">
    <div class="services-photo" role="img" aria-label="Blue-toned photograph of builders working on a timber roof frame"></div>
    <div class="services-content">
      <h2 class="services-title">Services We Offer:</h2>
      <ul class="services-list">
        <li>Home improvement projects</li>
        <li>House renovations</li>
        <li>Bathroom and kitchen</li>
        <li>Renovations</li>
        <li>House extensions</li>
        <li>New builds and granny flats</li>
      </ul>
    </div>
    <p class="services-brand">Stonebridge Building and Projects</p>
  </section>

  <section class="card card-contact">
    <div class="brand-lockup">
      <span class="brand-square"></span>
      <p class="brand-name">Stonebridge Building and Projects</p>
    </div>

    <div class="contact-person">
      <h1 class="person-name">Omar Haddani</h1>
      <p class="person-role">DIRECTOR</p>
    </div>

    <ul class="contact-list">
      <li>
        <svg class="contact-icon" viewBox="0 0 24 24"><circle cx="12" cy="12" r="12" fill="#4a4a4a"/><path d="M8.2 6.5l2 2.2-1.1 1.6c.8 1.7 2 2.9 3.6 3.7l1.6-1.1 2.2 2-1.3 2.1c-4.3-.3-8.2-4.2-8.5-8.5z" fill="#fff"/></svg>
        215 000 7272
      </li>
      <li>
        <svg class="contact-icon" viewBox="0 0 24 24"><rect x="1" y="5" width="22" height="14" fill="none" stroke="#4a4a4a" stroke-width="2"/><path d="M1 5l11 8 11-8M1 19l8-7M23 19l-8-7" fill="none" stroke="#4a4a4a" stroke-width="2"/></svg>
        omar@sbpbuilding.com.au
      </li>
      <li>
        <svg class="contact-icon" viewBox="0 0 24 24"><circle cx="12" cy="12" r="10" fill="none" stroke="#4a4a4a" stroke-width="2"/><ellipse cx="12" cy="12" rx="4.5" ry="10" fill="none" stroke="#4a4a4a" stroke-width="1.6"/><path d="M2 12h20M4 7h16M4 17h16" stroke="#4a4a4a" stroke-width="1.6"/></svg>
        sbpbuilding.com.au
      </li>
    </ul>

    <div class="social">
      <p>Find us on social</p>
      <p class="social-handle"><span class="social-dot"></span>sbp_building</p>
    </div>
  </section>

</body>
</html>
```